I would like a business card to match my truck wrap and logo. I would like the font to match my existing business card please.

Industry/Entity Type

Painter

Contact Information for Business Card

Rodrigo Fenwar 801-437-2190 Fenwarcoatings.utah@brelmox.com
SERVICES - Custom Paint & Stain, Interior & Exterior, Epoxy Coatings / Garage Floors, Cabinet Refinishing, Log Staining and Refinishing.

Requirements
Nice to have
• I would like to have the white and grey line like the bottom of my vehicle wrap, Light Grey to match my truck also.

```html
<!DOCTYPE html>
<html lang="en">
<head>
<meta charset="utf-8">
<title>Fenwar Painting – Business Card</title>
<link rel="stylesheet" href="https://fonts.googleapis.com/css2?family=Russo+One&family=Arimo:wght@400&display=swap">
<style>
  :root {
    --bg: #161616;
    --kraft-light: #dfbd8f;
    --kraft-mid: #c9a06c;
    --kraft-dark: #a67646;
    --ink: #111111;
  }
  * { margin: 0; padding: 0; box-sizing: border-box; }
  html, body { width: 1093px; height: 1200px; overflow: hidden; background: var(--bg); }
  .canvas { position: relative; width: 1093px; height: 1200px; }
  .card {
    position: absolute;
    left: 264px;
    width: 580px;
    height: 357px;
    background: linear-gradient(160deg, var(--kraft-light) 0%, var(--kraft-mid) 50%, var(--kraft-dark) 100%);
    color: var(--ink);
    box-shadow: 0 4px 10px rgba(0,0,0,.6);
  }
  .card--front { top: 226px; }
  .card--back { top: 620px; }
  .brand {
    position: absolute;
    left: 0; right: 0;
    top: 88px;
    display: flex;
    align-items: center;
    justify-content: center;
    gap: 14px;
  }
  .brand__mark { width: 34px; height: 34px; background: var(--ink); }
  .brand__name {
    font-family: "Russo One", sans-serif;
    font-size: 34px;
    letter-spacing: 1px;
    line-height: 1;
    color: var(--ink);
  }
  .holder {
    position: absolute; left: 0; right: 0; top: 213px;
    text-align: center;
    font-family: "Russo One", sans-serif;
    font-size: 23px;
    letter-spacing: .5px;
  }
  .divider {
    position: absolute; left: 229px; top: 252px;
    width: 120px; height: 1px; background: var(--ink); opacity: .7;
  }
  .contact {
    position: absolute; left: 0; right: 0; top: 264px;
    text-align: center;
    font-family: "Arimo", sans-serif;
    font-size: 18px;
    line-height: 23px;
  }
  .services {
    position: absolute; left: 0; right: 0; top: 255px;
    text-align: center;
    font-family: "Arimo", sans-serif;
    font-size: 17px;
    line-height: 21px;
  }
  .services .dot { font-size: 14px; }
</style>
</head>
<body>
<main class="canvas">
  <section class="card card--front">
    <div class="brand">
      <span class="brand__mark"></span>
      <span class="brand__name">FENWAR PAINTING</span>
    </div>
    <h1 class="holder">RODRIGO FENWAR</h1>
    <div class="divider"></div>
    <p class="contact">801-437-2190<br>Fenwarcoatings.utah@brelmox.com</p>
  </section>
  <section class="card card--back">
    <div class="brand">
      <span class="brand__mark"></span>
      <span class="brand__name">FENWAR PAINTING</span>
    </div>
    <p class="services">
      Custom Paint &amp; Stain <span class="dot">●</span> Interior &amp; Exterior<br>
      Epoxy Coatings / Garage Floors <span class="dot">●</span> Cabinet Refinishing<br>
      Log Staining and Refinishing.
    </p>
  </section>
</main>
</body>
</html>
```